Need Web Design for Business Process Outsourcing Company (Quorvane)

Quorvane is a business process outsourcing company. Need a simple site similar to http://www.tallowbrinkhire.com/ but with a more professional and credible look. New to the process; not sure where to start and comparing my options. Please let me know what my options are if I choose to go with you. Logo is attached for your reference. Please use same colorway

Reason: I want the final product to be coded. Please confirm you will be able to code final design.

Industry/Entity Type

Business

Coding

Coded - Design and coding required

```html
<!DOCTYPE html>
<html lang="en">
<head>
<meta charset="utf-8">
<title>Quorvane Services</title>
<link rel="stylesheet" href="https://fonts.googleapis.com/css2?family=Open+Sans:wght@400;600;700&family=Roboto+Condensed:wght@300;400;700&family=Oswald:wght@500&display=swap">
<style>
:root{
  --navy:#0b4c84;
  --navy-deep:#0d4f87;
  --accent:#0a8fd4;
  --ink:#333333;
  --body-text:#555555;
  --muted:#8a8a8a;
  --light:#ebebeb;
  --topbar:#eeeeee;
  --footer:#3d3d3d;
  --white:#ffffff;
}
*{box-sizing:border-box;margin:0;padding:0}
html,body{width:1200px;height:3689px;overflow:hidden}
body{font-family:"Open Sans",Arial,sans-serif;color:var(--body-text);background:var(--white)}
h1,h2,h3{font-weight:400}
.container{width:1048px;margin:0 auto;position:relative}
a{color:inherit;text-decoration:none}

/* top bar */
.topbar{height:44px;background:var(--topbar)}
.topbar .container{display:flex;justify-content:space-between;align-items:center;height:44px}
.social-mini{display:flex;gap:14px}
.social-mini span{width:14px;height:14px;border-radius:50%;background:var(--navy)}
.topbar-mail{display:flex;align-items:center;gap:12px;font-size:13px;color:var(--ink)}

/* header */
.header{height:81px}
.header .container{display:flex;justify-content:space-between;align-items:center;height:81px}
.brand{display:flex;align-items:center;gap:12px}
.brand-square{width:44px;height:44px;background:var(--accent)}
.brand-name{font-size:32px;font-weight:600;color:var(--navy)}
.call{display:flex;align-items:center;gap:12px}
.call-label{font-size:20px;color:var(--ink)}
.call-icon{width:48px;height:48px;border:2px solid var(--navy);border-radius:50%;display:flex;align-items:center;justify-content:center}
.call-number{font-size:25px;font-weight:700;color:var(--navy)}

/* nav */
.nav{height:55px;background:var(--navy)}
.nav ul{list-style:none;display:flex;height:55px;align-items:center;justify-content:space-between;padding-right:28px}
.nav li{font-size:14px;color:var(--white);text-transform:uppercase;height:55px;line-height:55px;padding:0 24px}
.nav li.active{background:#333;width:94px;text-align:center;padding:0}

/* hero */
.hero{height:575px;position:relative;background:linear-gradient(180deg,#c9dbe6 0%,#5f8fab 35%,#1f5f83 70%,#0f4566 100%);text-align:center}
.hero-title{position:absolute;left:50%;top:194px;transform:translateX(-50%);white-space:nowrap;padding:0 14px;height:66px;background:rgba(40,48,58,.62);color:var(--white);font-family:"Oswald",sans-serif;font-weight:500;font-size:50px;line-height:66px;letter-spacing:1px}
.hero-sub{position:absolute;left:50%;top:270px;transform:translateX(-50%);white-space:nowrap;width:350px;height:37px;background:rgba(90,110,125,.75);color:var(--white);font-size:20px;line-height:37px}
.hero-btn{position:absolute;left:499px;top:334px;width:202px;height:54px;background:var(--navy);color:var(--white);font-size:15px;font-weight:700;line-height:54px}

/* buttons */
.btn{display:inline-flex;align-items:center;gap:10px;background:var(--navy);color:var(--white);font-size:15px;text-transform:uppercase;height:51px;padding:0 26px}
.btn svg{width:14px;height:14px}

/* headings */
.section-title{font-family:"Roboto Condensed",sans-serif;font-weight:400;font-size:46px;color:var(--ink);text-transform:uppercase;text-align:center;line-height:1}
.section-title em{font-style:normal;color:var(--accent)}
.intro{font-size:13.5px;line-height:24px;text-align:center;color:var(--body-text)}

/* welcome */
.welcome{height:381px;padding-top:38px}
.welcome .section-title{text-align:left}
.welcome-text{width:681px;font-size:13.5px;line-height:22.5px;margin-top:30px}
.welcome .btn{margin-top:24px;width:172px;justify-content:center;padding:0}
.welcome-mark{position:absolute;left:720px;top:20px;width:300px;height:266px;display:flex;flex-direction:column;align-items:center;justify-content:center;gap:22px}
.welcome-mark .mark-square{width:150px;height:150px;background:var(--navy)}
.welcome-mark .mark-name{font-size:44px;font-weight:600;color:var(--accent)}

/* outsourcing */
.services{height:617px;background:var(--light);padding-top:38px;text-align:center}
.services .intro{margin-top:40px}
.service-grid{display:grid;grid-template-columns:repeat(4,1fr);gap:20px;margin-top:32px}
.service-icon{width:124px;height:124px;border-radius:50%;background:var(--accent);margin:0 auto;display:flex;align-items:center;justify-content:center}
.service-name{font-family:"Roboto Condensed",sans-serif;font-weight:400;font-size:21px;color:var(--navy);margin-top:22px}
.service-text{font-size:13.5px;line-height:25px;margin:8px auto 0;width:230px}
.services .btn{margin-top:40px}

/* experience */
.experience{height:554px;padding-top:40px;text-align:center}
.experience .intro{margin-top:42px}
.exp-grid{display:grid;grid-template-columns:repeat(4,236px);justify-content:space-between;margin-top:38px}
.exp-card{height:187px;position:relative}
.exp-photo{height:187px}
.exp-caption{position:absolute;left:0;right:0;bottom:0;height:52px;background:var(--navy);color:var(--white);font-family:"Roboto Condensed",sans-serif;font-size:21px;line-height:52px}
.experience .btn{margin-top:52px}

/* strategy */
.strategy{height:496px;background:var(--light);padding-top:40px;text-align:center}
.strategy .intro{margin-top:42px}
.strategy-grid{display:flex;margin-top:34px;text-align:left}
.strategy-item{display:flex;gap:20px;width:362px}
.strategy-item:last-child{width:auto}
.strategy-icon{width:128px;height:125px;background:var(--navy);flex:none;display:flex;align-items:center;justify-content:center}
.strategy-name{font-family:"Roboto Condensed",sans-serif;font-weight:400;font-size:21px;color:var(--navy);margin-top:12px}
.strategy-text{font-size:13.5px;line-height:25px;margin-top:8px;width:180px}
.strategy .btn{margin-top:50px}

/* security */
.security{height:123px;background:var(--accent)}
.security .container{display:flex;align-items:center;height:123px}
.security-lock{margin-left:67px;width:103px;height:110px}
.security-copy{margin-left:44px;color:var(--white);flex:1}
.security-title{font-family:"Roboto Condensed",sans-serif;font-weight:400;font-size:42px;line-height:1;text-transform:uppercase}
.security-text{font-size:13.5px;margin-top:4px}
.security-btn{width:150px;height:47px;background:var(--white);color:var(--navy);font-size:15px;text-transform:uppercase;text-align:center;line-height:47px;margin-right:69px}

/* news */
.news{height:499px;padding-top:46px}
.news-grid{display:grid;grid-template-columns:repeat(4,236px);justify-content:space-between;margin-top:56px}
.news-photo{height:141px}
.news-headline{font-size:13.5px;font-weight:400;line-height:26px;color:var(--navy);margin-top:14px}
.news-date{display:flex;align-items:center;gap:8px;font-size:12px;color:var(--muted);margin-top:2px}
.news-text{font-size:13.5px;line-height:25px;margin-top:8px}

/* footer */
.footer{height:209px;background:var(--footer);color:var(--white)}
.footer-top{display:flex;justify-content:space-between;align-items:center;height:67px;border-bottom:1px solid #5a5a5a}
.footer-links{display:flex;gap:26px;font-size:13px}
.footer-social{display:flex;gap:36px;padding-right:12px}
.footer-social span{width:18px;height:18px;border-radius:50%;background:var(--white)}
.footer-social span:first-child{background:var(--accent)}
.footer-heading{font-family:"Roboto Condensed",sans-serif;font-weight:400;font-size:21px;margin-top:26px}
.contact-row{display:flex;margin-top:18px;padding-left:10px}
.contact-item{display:flex;align-items:center;gap:14px;font-size:13px;line-height:20px}
.contact-item:nth-child(1){width:283px}
.contact-item:nth-child(2){width:275px}
.contact-item:nth-child(3){width:263px}
.contact-dot{width:38px;height:38px;border-radius:50%;background:var(--white);display:flex;align-items:center;justify-content:center;flex:none}
.contact-dot.pin{background:var(--accent)}
.copyright{height:55px;background:var(--navy-deep);color:var(--white);font-size:13px;text-align:center;line-height:55px}
.copyright b{font-weight:700}
</style>
</head>
<body>

<div class="topbar">
  <div class="container">
    <div class="social-mini"><span></span><span></span><span></span></div>
    <div class="topbar-mail">
      <svg width="16" height="12" viewBox="0 0 16 12"><rect width="16" height="12" fill="#0b4c84"/><path d="M0 0l8 6 8-6" fill="none" stroke="#fff" stroke-width="1.4"/></svg>
      Lorem Ipsum is simply
    </div>
  </div>
</div>

<header class="header">
  <div class="container">
    <div class="brand"><span class="brand-square"></span><span class="brand-name">Quorvane</span></div>
    <div class="call">
      <span class="call-label">Call us now</span>
      <span class="call-icon"><svg width="22" height="22" viewBox="0 0 24 24"><path d="M6.6 10.8a15 15 0 006.6 6.6l2.2-2.2a1 1 0 011-.25 11.4 11.4 0 003.6.57 1 1 0 011 1V20a1 1 0 01-1 1A17 17 0 013 4a1 1 0 011-1h3.5a1 1 0 011 1c0 1.25.2 2.45.57 3.57a1 1 0 01-.25 1z" fill="#333"/></svg></span>
      <span class="call-number">123 456 7890</span>
    </div>
  </div>
</header>

<nav class="nav">
  <div class="container">
    <ul>
      <li class="active">Home</li><li>Who We Are</li><li>Services</li><li>Strategy</li><li>Experience</li><li>Security</li><li>News</li><li>Contact Us</li>
    </ul>
  </div>
</nav>

<section class="hero" role="img" aria-label="Upward view of glass office towers against a pale sky">
  <h1 class="hero-title">QUORVANE SERVICES</h1>
  <p class="hero-sub">Lorem Ipsum is simply dummy</p>
  <a class="hero-btn">CONTACT US NOW</a>
</section>

<section class="welcome">
  <div class="container">
    <h2 class="section-title">Welcome to <em>Quorvane Services</em></h2>
    <p class="welcome-text">Lorem Ipsum is simply dummy text of the printing and typesetting industry. Lorem Ipsum has been the industry's standard dummy text ever since the 1500s, when an unknown printer took a galley of type and scrambled it to make a type specimen book. It has survived not only five centuries, but also the leap into electronic typesetting, remaining essentially unchanged. It was popularised in the 1960s with the release of Letraset sheets containing.</p>
    <a class="btn">Read More <svg viewBox="0 0 14 14"><path d="M2 2l5 5-5 5M7 2l5 5-5 5" fill="none" stroke="#fff" stroke-width="2"/></svg></a>
    <div class="welcome-mark"><span class="mark-square"></span><span class="mark-name">Quorvane</span></div>
  </div>
</section>

<section class="services">
  <div class="container">
    <h2 class="section-title">Outsourcing <em>Services</em></h2>
    <p class="intro">Lorem Ipsum is simply dummy text of the printing and typesetting industry.<br>Lorem Ipsum has a been the industry's standard.</p>
    <div class="service-grid">
      <div class="service">
        <div class="service-icon"><svg width="56" height="56" viewBox="0 0 24 24"><path d="M2 3h3l2.5 11h11l2-8H6.3" fill="none" stroke="#fff" stroke-width="1.8"/><circle cx="9" cy="19" r="1.8" fill="#fff"/><circle cx="17" cy="19" r="1.8" fill="#fff"/><path d="M9 8v4M12 8v4M15 8v4" stroke="#fff" stroke-width="1.2"/></svg></div>
        <h3 class="service-name">Customer Service</h3>
        <p class="service-text">Lorem Ipsum is simply dummy text of the printing and typesetting industry.</p>
      </div>
      <div class="service">
        <div class="service-icon"><svg width="56" height="56" viewBox="0 0 24 24"><path d="M5 13v-2a7 7 0 0114 0v2" fill="none" stroke="#fff" stroke-width="1.8"/><rect x="3.5" y="11.5" width="3.5" height="6" rx="1" fill="#fff"/><rect x="17" y="11.5" width="3.5" height="6" rx="1" fill="#fff"/><path d="M18.7 17.5c0 2-2 3-5 3" fill="none" stroke="#fff" stroke-width="1.4"/></svg></div>
        <h3 class="service-name">Ecommerce</h3>
        <p class="service-text">Lorem Ipsum is simply dummy text of the printing and typesetting industry.</p>
      </div>
      <div class="service">
        <div class="service-icon"><svg width="56" height="56" viewBox="0 0 24 24"><path d="M12 5a5 5 0 00-3 9v2h6v-2a5 5 0 00-3-9z" fill="#fff"/><rect x="9" y="17" width="6" height="1.6" fill="#fff"/><rect x="10" y="19.4" width="4" height="1.6" fill="#fff"/><path d="M12 1v2M4 4l1.4 1.4M20 4l-1.4 1.4M1 11h2M21 11h2" stroke="#fff" stroke-width="1.4"/></svg></div>
        <h3 class="service-name">Creative</h3>
        <p class="service-text">Lorem Ipsum is simply dummy text of the printing and typesetting industry.</p>
      </div>
      <div class="service">
        <div class="service-icon"><svg width="56" height="56" viewBox="0 0 24 24"><rect x="5" y="2" width="14" height="4.5" fill="#fff"/><rect x="5" y="8" width="14" height="4.5" fill="#fff"/><rect x="5" y="14" width="14" height="4.5" fill="#fff"/><circle cx="8" cy="4.2" r=".9" fill="#0a8fd4"/><circle cx="8" cy="10.2" r=".9" fill="#0a8fd4"/><circle cx="8" cy="16.2" r=".9" fill="#0a8fd4"/><path d="M12 18.5v3M6 21.5h12" stroke="#fff" stroke-width="1.4"/></svg></div>
        <h3 class="service-name">IT Solutions</h3>
        <p class="service-text">Lorem Ipsum is simply dummy text of the printing and typesetting industry.</p>
      </div>
    </div>
    <a class="btn">View All <svg viewBox="0 0 14 14"><path d="M2 2l5 5-5 5M7 2l5 5-5 5" fill="none" stroke="#fff" stroke-width="2"/></svg></a>
  </div>
</section>

<section class="experience">
  <div class="container">
    <h2 class="section-title">Our <em>Experience</em></h2>
    <p class="intro">Lorem Ipsum is simply dummy text of the printing and typesetting industry. Lorem Ipsum has been the<br>industry's standard dummy text ever since the 1500s.</p>
    <div class="exp-grid">
      <div class="exp-card"><div class="exp-photo" role="img" aria-label="Team meeting around an office table" style="background:linear-gradient(135deg,#d8d4cf,#8c8079)"></div><div class="exp-caption">Lorem Ipsum is simply</div></div>
      <div class="exp-card"><div class="exp-photo" role="img" aria-label="Magnifying glass over a financial chart" style="background:linear-gradient(135deg,#e6eef5,#7fa1bd)"></div><div class="exp-caption">Lorem Ipsum is simply</div></div>
      <div class="exp-card"><div class="exp-photo" role="img" aria-label="Presentation with a chart board" style="background:linear-gradient(135deg,#f2f2f2,#b7b7b7)"></div><div class="exp-caption">Lorem Ipsum is simply</div></div>
      <div class="exp-card"><div class="exp-photo" role="img" aria-label="Hands reviewing documents on a desk" style="background:linear-gradient(135deg,#6b5d52,#a89a8c)"></div><div class="exp-caption">Lorem Ipsum is simply</div></div>
    </div>
    <a class="btn">View All <svg viewBox="0 0 14 14"><path d="M2 2l5 5-5 5M7 2l5 5-5 5" fill="none" stroke="#fff" stroke-width="2"/></svg></a>
  </div>
</section>

<section class="strategy">
  <div class="container">
    <h2 class="section-title">Our <em>Strategy</em></h2>
    <p class="intro">Lorem Ipsum is simply dummy text of the printing and typesetting industry. Lorem Ipsum has been the<br>industry's standard dummy text ever since the 1500s.</p>
    <div class="strategy-grid">
      <div class="strategy-item">
        <div class="strategy-icon"><svg width="64" height="64" viewBox="0 0 24 24"><circle cx="10" cy="10" r="6" fill="none" stroke="#fff" stroke-width="2"/><path d="M14.5 14.5L21 21" stroke="#fff" stroke-width="2.6"/></svg></div>
        <div><h3 class="strategy-name">Lorem Ipsum</h3><p class="strategy-text">Lorem Ipsum is simply dummy text of the print ing and typesetting...</p></div>
      </div>
      <div class="strategy-item">
        <div class="strategy-icon"><svg width="64" height="64" viewBox="0 0 24 24"><rect x="3" y="3" width="18" height="12" fill="none" stroke="#fff" stroke-width="1.8"/><path d="M6 12l4-4 3 2 5-5" fill="none" stroke="#fff" stroke-width="1.6"/><path d="M12 15v5M8 21l4-3 4 3" fill="none" stroke="#fff" stroke-width="1.6"/></svg></div>
        <div><h3 class="strategy-name">Lorem Ipsum</h3><p class="strategy-text">Lorem Ipsum is simply dummy text of the print ing and typesetting...</p></div>
      </div>
      <div class="strategy-item">
        <div class="strategy-icon"><svg width="64" height="64" viewBox="0 0 24 24"><circle cx="12" cy="12" r="4" fill="none" stroke="#fff" stroke-width="2.2"/><path d="M12 3v3M12 18v3M3 12h3M18 12h3M5.6 5.6l2.1 2.1M16.3 16.3l2.1 2.1M5.6 18.4l2.1-2.1M16.3 7.7l2.1-2.1" stroke="#fff" stroke-width="2.2"/></svg></div>
        <div><h3 class="strategy-name">Lorem Ipsum</h3><p class="strategy-text">Lorem Ipsum is simply dummy text of the print ing and typesetting...</p></div>
      </div>
    </div>
    <a class="btn">Know More <svg viewBox="0 0 14 14"><path d="M2 2l5 5-5 5M7 2l5 5-5 5" fill="none" stroke="#fff" stroke-width="2"/></svg></a>
  </div>
</section>

<section class="security">
  <div class="container">
    <svg class="security-lock" viewBox="0 0 100 110"><path d="M25 48V32a25 25 0 0150 0v16" fill="none" stroke="#c9d3db" stroke-width="10"/><rect x="12" y="46" width="76" height="58" rx="6" fill="#e3e8ec"/><path d="M32 74l13 13 24-24" fill="none" stroke="#0b4c84" stroke-width="8"/></svg>
    <div class="security-copy">
      <h2 class="security-title">Security</h2>
      <p class="security-text">Lorem Ipsum is simply dummy text of the printing and typesetting industry.</p>
    </div>
    <a class="security-btn">Contact Us</a>
  </div>
</section>

<section class="news">
  <div class="container">
    <h2 class="section-title">Latest <em>News</em></h2>
    <div class="news-grid">
      <article>
        <div class="news-photo" role="img" aria-label="Businessman working at a laptop" style="background:linear-gradient(135deg,#f0f0f0,#9aa3ab)"></div>
        <h3 class="news-headline">Lorem Ipsum is simply dummy text of the printing.</h3>
        <p class="news-date"><svg width="11" height="11" viewBox="0 0 12 12"><rect x="1" y="2" width="10" height="9" fill="none" stroke="#8a8a8a"/><path d="M1 4.5h10" stroke="#8a8a8a"/></svg>November 14, 2016</p>
        <p class="news-text">Lorem Ipsum is simply dummy text of the printing and typesetting industry.</p>
      </article>
      <article>
        <div class="news-photo" role="img" aria-label="Sticky notes arranged on a planning board" style="background:linear-gradient(135deg,#d9c9b4,#8e8577)"></div>
        <h3 class="news-headline">Lorem Ipsum is simply dummy text of the printing.</h3>
        <p class="news-date"><svg width="11" height="11" viewBox="0 0 12 12"><rect x="1" y="2" width="10" height="9" fill="none" stroke="#8a8a8a"/><path d="M1 4.5h10" stroke="#8a8a8a"/></svg>November 14, 2016</p>
        <p class="news-text">Lorem Ipsum is simply dummy text of the printing and typesetting industry.</p>
      </article>
      <article>
        <div class="news-photo" role="img" aria-label="Business handshake in an office" style="background:linear-gradient(135deg,#c7d4de,#3f5666)"></div>
        <h3 class="news-headline">Lorem Ipsum is simply dummy text of the printing.</h3>
        <p class="news-date"><svg width="11" height="11" viewBox="0 0 12 12"><rect x="1" y="2" width="10" height="9" fill="none" stroke="#8a8a8a"/><path d="M1 4.5h10" stroke="#8a8a8a"/></svg>November 14, 2016</p>
        <p class="news-text">Lorem Ipsum is simply dummy text of the printing and typesetting industry.</p>
      </article>
      <article>
        <div class="news-photo" role="img" aria-label="Pen pointing at printed charts" style="background:linear-gradient(135deg,#e9f0f6,#6f94b4)"></div>
        <h3 class="news-headline">Lorem Ipsum is simply dummy text of the printing.</h3>
        <p class="news-date"><svg width="11" height="11" viewBox="0 0 12 12"><rect x="1" y="2" width="10" height="9" fill="none" stroke="#8a8a8a"/><path d="M1 4.5h10" stroke="#8a8a8a"/></svg>November 14, 2016</p>
        <p class="news-text">Lorem Ipsum is simply dummy text of the printing and typesetting industry.</p>
      </article>
    </div>
  </div>
</section>

<footer class="footer">
  <div class="container">
    <div class="footer-top">
      <nav class="footer-links"><a>Home</a><a>Who We Are</a><a>Services</a><a>Strategy</a><a>Experience</a><a>Security</a><a>News</a><a>Contact Us</a></nav>
      <div class="footer-social"><span></span><span></span><span></span></div>
    </div>
    <h2 class="footer-heading">Contact Us</h2>
    <div class="contact-row">
      <div class="contact-item"><span class="contact-dot pin"><svg width="16" height="20" viewBox="0 0 16 20"><path d="M8 0a7 7 0 00-7 7c0 5 7 13 7 13s7-8 7-13a7 7 0 00-7-7z" fill="#fff"/><circle cx="8" cy="7" r="2.6" fill="#0a8fd4"/></svg></span><span>Lorem Ipsum is simply<br>dummy text of the.</span></div>
      <div class="contact-item"><span class="contact-dot"><svg width="14" height="20" viewBox="0 0 14 20"><rect x="1" y="1" width="12" height="18" rx="2" fill="none" stroke="#3d3d3d" stroke-width="2"/><circle cx="7" cy="16" r="1.2" fill="#3d3d3d"/></svg></span><span>123 456 7890</span></div>
      <div class="contact-item"><span class="contact-dot"><svg width="18" height="18" viewBox="0 0 18 18"><rect x="1" y="6" width="16" height="11" fill="#3d3d3d"/><rect x="4" y="1" width="10" height="6" fill="none" stroke="#3d3d3d" stroke-width="1.6"/><rect x="5" y="10" width="8" height="2" fill="#fff"/></svg></span><span>123 456 7890</span></div>
      <div class="contact-item"><span class="contact-dot"><svg width="18" height="13" viewBox="0 0 18 13"><rect x="1" y="1" width="16" height="11" fill="none" stroke="#3d3d3d" stroke-width="1.6"/><path d="M1 1l8 6 8-6" fill="none" stroke="#3d3d3d" stroke-width="1.6"/></svg></span><span>Lorem Ipsum is simply</span></div>
    </div>
  </div>
</footer>

<div class="copyright">© <b>QUORVANE SERVICES - 2016.</b> All Rights Reserved.</div>

</body>
</html>
```